Tellmora Corporate Stationery

Look for design of all new corporate stationery for an existing insurance broking business that is going through a redesign and move from older partners to younger family members. New Logo is attached. Company is Brisbane based.
Colours in the Logo is Hex #43bed8 and website features a lot of hex #17b8d8. Website front page "A plan to protect you" - headline. "Professional and Individual advice to protect your greatest assets" - tagline.

Stationery required: Business Cards, Letter head, Thank-you cards, Birthday cards, Presentation folders, With Compliment slips and a powerpoint template. We also would like to send a card to all customers with the something along of the lines of "something new".

Target Market(s)

Customers of Insurance business looking at superannuation, life and income protection insurance, investment advice and wills

Industry/Entity Type

Insurance Broker

Font styles to use
Other font styles liked:
• same as logo

Requirements
Must have
• The above designs for new stationery for the new business including:
• Business Cards, Letter head, Thank-you cards, Birthday cards, Presentation folders, With Compliment slips and a powerpoint template. We also would like to send a card to all customers with the something along of the lines of "something new".
Nice to have
• It is a new look - long time family business being passed to next generation - big focus on advice for YOU, individual advice etc..

```html
<!DOCTYPE html>
<html lang="en">
<head>
<meta charset="utf-8">
<title>Tellmora Business Card</title>
<link rel="stylesheet" href="https://fonts.googleapis.com/css2?family=Open+Sans:ital,wght@0,400;0,600;1,400&display=swap">
<style>
  :root {
    --teal: #3fc0d9;
    --teal-soft: #43bed8;
    --grey-text: #6b6b6d;
    --grey-rule: #8a8a8c;
    --grey-band: #7d7d80;
    --card-white: #ffffff;
    --stage: #262626;
  }
  * { margin: 0; padding: 0; box-sizing: border-box; }
  html, body {
    width: 1200px; height: 987px; overflow: hidden;
    background: var(--stage);
    font-family: "Open Sans", sans-serif;
  }
  .card {
    position: absolute; left: 293px; width: 615px; height: 352px; overflow: hidden;
  }
  .card--front { top: 130px; background: var(--card-white); }
  .card--back { top: 505px; background: var(--teal); }

  .brand {
    position: absolute; display: flex; align-items: center; gap: 14px;
    font-weight: 600; letter-spacing: 1px; text-transform: uppercase; line-height: 1;
  }
  .brand__dot { border-radius: 50%; flex: none; }
  .card--front .brand { right: 30px; top: 62px; font-size: 30px; color: var(--teal); }
  .card--front .brand__dot { width: 40px; height: 40px; background: var(--grey-band); }
  .card--back .brand { right: 29px; top: 258px; font-size: 34px; color: var(--card-white); }
  .card--back .brand__dot { width: 44px; height: 44px; background: var(--card-white); }

  .holder { position: absolute; left: 27px; top: 195px; }
  .holder__name { font-size: 21px; font-weight: 600; color: var(--teal); letter-spacing: .3px; line-height: 1.1; }
  .holder__role { font-size: 16px; color: var(--grey-text); margin-top: 3px; }
  .rule { position: absolute; left: 27px; width: 559px; top: 250px; height: 1px; background: var(--grey-rule); }

  .contact { position: absolute; top: 262px; font-size: 16px; color: var(--grey-text); line-height: 23px; }
  .contact--address { left: 30px; }
  .contact--phones { left: 246px; }
  .contact--digital { left: 396px; }
  .contact__line { display: flex; align-items: center; gap: 7px; white-space: nowrap; }
  .icon { width: 15px; height: 15px; fill: var(--teal); flex: none; }

  .footer-bands { position: absolute; left: 0; bottom: 0; width: 615px; height: 36px; }
  .web {
    position: absolute; font-style: italic; letter-spacing: 3.4px; font-size: 15px; color: var(--card-white);
  }
  .card--front .web { left: 384px; top: 326px; }
  .card--back .web { right: 29px; top: 316px; font-size: 16px; }
</style>
</head>
<body>

<section class="card card--front" aria-label="Business card front">
  <div class="brand"><span class="brand__dot"></span>Tellmora</div>

  <div class="holder">
    <div class="holder__name">AARON VALE</div>
    <div class="holder__role">CEO/FOUNDER</div>
  </div>
  <div class="rule"></div>

  <div class="contact contact--address">
    <div>42 Wattle Grove Road</div>
    <div>Brisbane, Queensland 4000</div>
  </div>

  <div class="contact contact--phones">
    <div class="contact__line">
      <svg class="icon" viewBox="0 0 24 24"><path d="M6.6 10.8a15.1 15.1 0 0 0 6.6 6.6l2.2-2.2c.3-.3.7-.4 1-.2 1.1.4 2.3.6 3.6.6.6 0 1 .4 1 1V20c0 .6-.4 1-1 1C10.6 21 3 13.4 3 4c0-.6.4-1 1-1h3.5c.6 0 1 .4 1 1 0 1.3.2 2.5.6 3.6.1.3 0 .7-.2 1z"/></svg>
      07 3184 5620
    </div>
    <div class="contact__line">
      <svg class="icon" viewBox="0 0 24 24"><path d="M7 1h10a2 2 0 0 1 2 2v18a2 2 0 0 1-2 2H7a2 2 0 0 1-2-2V3a2 2 0 0 1 2-2zm0 3v15h10V4zm5 16.2a1 1 0 1 0 0 .1z"/></svg>
      0412 587 903
    </div>
  </div>

  <div class="contact contact--digital">
    <div class="contact__line">
      <svg class="icon" viewBox="0 0 24 24"><path d="M6 2h12v5H6zM3 8h18a2 2 0 0 1 2 2v7h-4v5H5v-5H1v-7a2 2 0 0 1 2-2zm4 8v4h10v-4z"/></svg>
      07 3184 5621
    </div>
    <div class="contact__line">
      <svg class="icon" viewBox="0 0 24 24"><path d="M2 5h20v14H2zm2 2v.5l8 5 8-5V7zm0 3v7h16v-7l-8 5z"/></svg>
      hello@tellmora.com
    </div>
  </div>

  <svg class="footer-bands" viewBox="0 0 615 36" preserveAspectRatio="none">
    <path d="M0 17 H336 Q346 17 350 12 L350 22 Q344 25 334 25 H0 Z" fill="var(--grey-band)"/>
    <path d="M337 36 Q350 36 354 22 Q358 3 376 3 H615 V36 Z" fill="var(--teal)"/>
    <rect x="0" y="26" width="615" height="10" fill="var(--teal)"/>
  </svg>
  <div class="web">www.tellmora.com</div>
</section>

<section class="card card--back" aria-label="Business card back">
  <div class="brand"><span class="brand__dot"></span>Tellmora</div>
  <div class="web">www.tellmora.com</div>
</section>

</body>
</html>
```